Harrowgate Care Assurance Ltd needs a business card and logo

We need a logo for documents, invoices etc and a business card to match. We are a health auditing, training and consulting company based in NZ and working in both Australia and NZ. We ensure health organisations meet all their compliance requirements and develop expertise in the health auditing sector. The design should in some way reflect either symbols for quality management in the health sector.

Target Market(s)

Health providers and those wishing to increase their capability in meeting and understanding compliance requirements

Industry/Entity Type

Business

Contact Information for Business Card

Logo plus contact details

Logo Text

Health auditing, consultancy and training

Requirements
Must have
• Name and contact details director: Marla Fenwick, mfenwick@hca-example.co.nz, PO Box 318, Warkworth, NZ, cell +6427391652

```html
<!DOCTYPE html>
<html lang="en">
<head>
<meta charset="utf-8">
<title>Harrowgate Care Assurance Ltd – Business Card</title>
<link rel="stylesheet" href="https://fonts.googleapis.com/css2?family=Josefin+Sans:wght@600&family=Old+Standard+TT:wght@400&display=swap">
<style>
  :root {
    --page: #e9e9e7;
    --card: #f7f7f6;
    --green: #7cc142;
    --green-light: #a6d86c;
    --blue: #2a9fd6;
    --orange: #ee8a1e;
    --magenta: #d81b63;
    --ink: #ffffff;
    --logo-ink: #4a4a4a;
    --faint: #eceae4;
  }
  * { margin: 0; padding: 0; box-sizing: border-box; }
  html, body {
    width: 1200px; height: 900px; overflow: hidden;
    background: var(--page);
  }
  .card {
    position: absolute; left: 100px; top: 160px;
    width: 1000px; height: 580px;
    background: var(--card);
    overflow: hidden;
    box-shadow: 0 4px 14px rgba(0,0,0,.12);
  }
  .brand {
    position: absolute; left: 150px; top: 58px;
    display: flex; align-items: center; gap: 14px;
  }
  .brand-dot {
    width: 34px; height: 34px; border-radius: 50%;
    background: var(--green);
    flex: none;
  }
  .brand-name {
    font-family: "Josefin Sans", sans-serif; font-weight: 600;
    font-size: 24px; line-height: 1.2; color: var(--logo-ink);
    letter-spacing: .5px; width: 240px;
  }
  .watermark-circle {
    position: absolute; left: 660px; top: 70px;
    width: 330px; height: 330px; border-radius: 50%;
    background: var(--faint);
    opacity: .8;
  }
  .band {
    position: absolute; left: 0;
    height: 58px;
    background: linear-gradient(90deg, var(--green) 0%, var(--green-light) 100%);
    clip-path: polygon(0 0, calc(100% - 38px) 0, 100% 50%, calc(100% - 38px) 100%, 0 100%);
    display: flex; align-items: center; gap: 14px;
    padding-left: 40px;
    color: var(--ink);
  }
  .band--name { top: 200px; width: 560px; }
  .band--phone { top: 268px; width: 620px; }
  .band--email { top: 336px; width: 700px; }
  .band--address { top: 404px; width: 740px; }
  .person-name {
    font-family: "Josefin Sans", sans-serif; font-weight: 600;
    font-size: 34px; font-variant: small-caps; letter-spacing: 1px;
    padding-top: 6px;
  }
  .contact-text {
    font-family: "Old Standard TT", serif;
    font-size: 30px; letter-spacing: .5px;
  }
  .icon { flex: none; }
  .colour-strip {
    position: absolute; left: 0; bottom: 0; width: 100%; height: 40px;
    display: flex;
  }
  .colour-strip span { height: 100%; }
  .strip-green { width: 27%; background: var(--green); }
  .strip-blue { width: 26%; background: var(--blue); }
  .strip-orange { width: 27%; background: var(--orange); }
  .strip-magenta { width: 20%; background: var(--magenta); }
</style>
</head>
<body>
  <main class="card">
    <div class="watermark-circle" aria-hidden="true"></div>

    <div class="brand">
      <span class="brand-dot" aria-hidden="true"></span>
      <span class="brand-name">Harrowgate Care Assurance Ltd</span>
    </div>

    <div class="band band--name">
      <span class="person-name">Marla Fenwick</span>
    </div>

    <div class="band band--phone">
      <svg class="icon" width="34" height="34" viewBox="0 0 34 34" aria-label="Phone">
        <rect x="1" y="1" width="32" height="32" rx="7" fill="#fff"/>
        <path d="M11 8c1.5-1 3 2 3.6 3.4.4 1-1.4 2-1.2 2.8.6 2 2.4 4 4.4 5 .8.3 1.8-1.6 2.8-1.2 1.4.6 4.4 2.2 3.4 3.6-1 1.6-2.6 2.6-4.4 2.2C14 22.6 10 18 8.6 12.8 8.2 11 9.4 9 11 8z" fill="var(--green)"/>
      </svg>
      <span class="contact-text">: +6427391652</span>
    </div>

    <div class="band band--email">
      <svg class="icon" width="46" height="32" viewBox="0 0 46 32" aria-label="Email">
        <rect x="2" y="2" width="42" height="28" rx="2" fill="none" stroke="#fff" stroke-width="3"/>
        <path d="M3 3 23 19 43 3" fill="none" stroke="#fff" stroke-width="3"/>
      </svg>
      <span class="contact-text">: mfenwick@hca-example.co.nz</span>
    </div>

    <div class="band band--address">
      <span class="contact-text">PO Box 318, Warkworth, NZ,</span>
    </div>

    <div class="colour-strip" aria-hidden="true">
      <span class="strip-green"></span>
      <span class="strip-blue"></span>
      <span class="strip-orange"></span>
      <span class="strip-magenta"></span>
    </div>
  </main>
</body>
</html>
```